Business Card - high end, modern health care

Hey designers!

We need a double sided business card for the boutique, cutting edge physical therapy rehabilitation centre in Sydney's Northern Beaches.

With the most qualified physios in the area The Harbourview Motion Clinic does what other physiotherapy practices do not, we take our time with our patients giving them longer appointments, better physios and therefor faster results!

We guarantee that the service people receive at THMC will be unparalleled.

Hence we need a business card to reflect our modern, boutique, high end service. The final design needs to reflect that we are in a class of our own yet with the feel of beachside retreat.

Below I have attached our logo in both blue on white and white on blue. The exact colour is;
and the font that we have used in our logo is Tex Gyre Aventador.

I like the idea of the blue as the main colour as it is more eye catching and our signage onto the main road will be in this blue and in the interest of consistency across marketing the blue needs to be a part of the design. However I would appreciate a few designs onto a wooden background as this is a visual theme within the fitout of the practice.

The design needs to be of standard size (91x55mm).

Target Market(s)

We target people who have an end outcome in mind and those who have had poor experiences with other providers and ensure that everyone gets the care that they deserve with a premium service that is tailored to the individuals circumstances. As a premium service, the target market is highly educated, business and tech savvy with the additional target market of elderly people who have self funded their retirement and see value in paying for the best ongoing rehabilitation to maintain independence.

Industry/Entity Type

Physical Therapy

Contact Information for Business Card

Name, designation( Titled Musculoskeletal Physiotherapist... there will also be those in the company that have multiple designations ie 5 or 6 words long), phone number, email, facebook, instagram, address

Font styles to use
Sans Serif

Colors

Designer to choose colors to be used in the design.

Requirements
Must have
• Front - The logo as large as possible, blue or wooden theme, and all of the important details.
• Back - A blank space/lines on which to write appointment times (no "Appointment, date, time" etc.)
Nice to have
• facebook url
• logos for facebook and instagram
• Mini logos for the phone and email?

```html
<!DOCTYPE html>
<html lang="en">
<head>
<meta charset="utf-8">
<title>The Harbourview Motion Clinic – Business Card</title>
<link href="https://fonts.googleapis.com/css2?family=Raleway:wght@400;500;600&display=swap" rel="stylesheet">
<style>
  :root {
    --brand-blue: #0d57a6;
    --brand-blue-soft: #2f6bb3;
    --ink: #1b1b1b;
    --rule: #3a3a3a;
    --dash: #8a8a8a;
    --paper: #ffffff;
    --backdrop: #57546f;
    --social-a: #2d8fd5;
    --social-b: #e86a9a;
  }
  * { margin: 0; padding: 0; box-sizing: border-box; }
  html, body { width: 1200px; height: 1000px; overflow: hidden; }
  body {
    background: var(--backdrop);
    font-family: "Raleway", sans-serif;
    position: relative;
  }
  .card {
    position: absolute;
    width: 658px;
    height: 375px;
    overflow: hidden;
    box-shadow: 0 6px 18px rgba(0,0,0,.35);
  }
  .card-front { left: 136px; top: 78px; background: var(--brand-blue); }
  .card-back { left: 437px; top: 548px; background: var(--paper); color: var(--ink); }

  .front-decor { position: absolute; left: 282px; top: 4px; }
  .brand {
    position: absolute; left: 48px; top: 156px;
    display: flex; align-items: center; gap: 10px;
    color: #fff; font-weight: 600;
  }
  .brand-mark { width: 56px; height: 56px; border-radius: 50%; background: #fff; flex: none; }
  .brand-name { line-height: 1; }
  .brand-name .line-1 { display: block; font-size: 30px; letter-spacing: .5px; }
  .brand-name .line-2 { display: block; font-size: 19px; letter-spacing: 5.2px; margin-top: 5px; }

  .person-name { position: absolute; left: 43px; top: 64px; font-size: 26px; font-weight: 500; }
  .person-name .accent { color: var(--brand-blue); }
  .person-title { position: absolute; left: 43px; top: 101px; font-size: 15px; }
  .back-mark { position: absolute; left: 531px; top: 42px; width: 82px; height: 82px; border-radius: 50%; background: var(--brand-blue); }
  .rule { position: absolute; left: 43px; width: 571px; height: 1.5px; background: var(--rule); }
  .rule-top { top: 138px; }
  .rule-bottom { top: 227px; }

  .contact { position: absolute; display: flex; align-items: center; gap: 14px; font-size: 18px; }
  .contact svg { flex: none; }
  .contact-phone { left: 43px; top: 157px; }
  .contact-email { left: 43px; top: 189px; }
  .social { position: absolute; left: 441px; display: flex; align-items: center; gap: 9px; font-size: 15px; }
  .social .dot { width: 22px; height: 22px; border-radius: 50%; }
  .social-profile { top: 158px; }
  .social-profile .dot { background: var(--social-a); }
  .social-gallery { top: 190px; }
  .social-gallery .dot { background: var(--social-b); }

  .address { position: absolute; left: 43px; top: 240px; font-size: 15px; }
  .write-line { position: absolute; display: flex; align-items: flex-end; gap: 8px; font-size: 15px; }
  .write-line .blank { border-bottom: 1.5px dashed var(--dash); height: 1px; margin-bottom: 4px; }
  .appointment { left: 43px; top: 283px; }
  .appointment .blank { width: 466px; }
  .date { left: 43px; top: 321px; }
  .date .blank { width: 266px; }
  .time { left: 355px; top: 321px; }
  .time .blank { width: 214px; }
</style>
</head>
<body>
  <section class="card card-front" aria-label="Card front">
    <svg class="front-decor" width="340" height="340" viewBox="0 0 340 340" aria-hidden="true">
      <circle cx="170" cy="170" r="166" fill="var(--brand-blue-soft)" opacity=".55"/>
    </svg>
    <div class="brand">
      <span class="brand-mark" aria-hidden="true"></span>
      <span class="brand-name">
        <span class="line-1">THE HARBOURVIEW</span>
        <span class="line-2">MOTION CLINIC</span>
      </span>
    </div>
  </section>

  <section class="card card-back" aria-label="Card back">
    <h1 class="person-name">Name of <span class="accent">Person</span></h1>
    <p class="person-title">Musculoskeletal Physiotherapist</p>
    <span class="back-mark" aria-hidden="true"></span>
    <div class="rule rule-top"></div>

    <div class="contact contact-phone">
      <svg width="22" height="22" viewBox="0 0 24 24" aria-hidden="true">
        <circle cx="12" cy="12" r="10.5" fill="none" stroke="#111" stroke-width="2"/>
        <path d="M8.4 6.6l1.6-.4 1.2 2.6-1 1c.6 1.4 1.6 2.4 3 3l1-1 2.6 1.2-.4 1.6c-.2.6-.8 1-1.5.9-3.7-.5-6.9-3.7-7.4-7.4-.1-.7.3-1.3.9-1.5z" fill="#111"/>
      </svg>
      <span>555.018.2046</span>
    </div>
    <div class="contact contact-email">
      <svg width="22" height="16" viewBox="0 0 22 16" aria-hidden="true">
        <rect width="22" height="16" fill="#111"/>
        <path d="M0 0l11 9 11-9" fill="none" stroke="#fff" stroke-width="1.5"/>
      </svg>
      <span>companyname@email.com</span>
    </div>
    <div class="social social-profile"><span class="dot" aria-hidden="true"></span><span>profile/name</span></div>
    <div class="social social-gallery"><span class="dot" aria-hidden="true"></span><span>gallery_name</span></div>

    <div class="rule rule-bottom"></div>
    <p class="address">No.01, Adrs line 01, Adrs line 02, Street, City, Country.</p>

    <div class="write-line appointment"><span>Appointment</span><span class="blank"></span></div>
    <div class="write-line date"><span>Date</span><span class="blank"></span></div>
    <div class="write-line time"><span>Time</span><span class="blank"></span></div>
  </section>
</body>
</html>
```